Harbor Seal Works Spray Foam Appications website

We need a custom website for our company, www.harborsealworks.example. We need something we can modify by adding/changing content, photos, updated projects, etc. We are a commercial contractor specializing in Spray Foam applications. We want the website to be very creative and easy to navigate. The main points of the website are to showcase our projects, and describe our scope of services. We provide spray foam applications to the residential and commercial market. We offer Spray Foam roofing applications, as well as Spray Foam interior insulation applications. We also provide Roof Restoration Coating Systems to refurbish old and failing metal roofs. We would be ok with a one page web design if we can get the scope of our services to flow in a single page. The designer can decide if single or multiple pages works best for our business. One of the suppliers we work with is www.verdansupply.example.

Target Market(s)

Residential Home Builders, General Contractors, Commercial Construction Companies, Property Management Groups.

Industry/Entity Type

Insulation

Number of Pages Required

5+ page

Font styles to use
Serif
Sans Serif

Colors

Designer to choose colors to be used in the design.

Requirements
Must have
• We already have a Wix page, so website must be a Wix theme design. Nice easy to navigate format. Color matched to our current logo theme. We already have brochures and would like for it to match what's already in the hands of some of our customers. Need to be able to manage content to update photos, projects, scope of service, etc., via Wix. Current hold/splash page is hosted at www.harborsealworks.example. We would also like to have this video posted on the home page: https://www.videohost.example/watch?v=QxT4pLm9ZrA&feature=share
Nice to have
• I have attached some splash videos, being able to incorporate these somehow without being overpowering would be nice.

```html
<!DOCTYPE html>
<html lang="en">
<head>
<meta charset="utf-8">
<title>Harbor Seal Works — Spray Foam &amp; Roof Restoration</title>
<link rel="stylesheet" href="https://fonts.googleapis.com/css2?family=Montserrat:wght@400;500;600;700&family=Raleway:wght@400;500;600&family=Fira+Sans+Condensed:wght@400&display=swap">
<style>
:root{
  --gold:#f4b11b;
  --gold-light:#f6bd3f;
  --black:#000;
  --charcoal:#222;
  --footer:#1b1b1b;
  --white:#fff;
  --muted:#9a9a9a;
  --head:'Montserrat',sans-serif;
  --body:'Raleway',sans-serif;
}
*{margin:0;padding:0;box-sizing:border-box}
html,body{width:1200px;height:3750px;overflow:hidden;background:var(--black);color:var(--white);font-family:var(--body)}
.page{position:relative;width:1200px;height:3750px}
section,header,footer{position:relative;width:1200px}
.abs{position:absolute}
.label{font-family:var(--head);font-size:10px;letter-spacing:2px;color:var(--gold);text-transform:uppercase;font-weight:500}
.title{font-family:var(--head);font-weight:600;font-size:25px}
.center{left:0;width:1200px;text-align:center}
.btn{position:absolute;display:flex;align-items:center;justify-content:center;font-family:var(--head);font-size:9px;font-weight:600;letter-spacing:1px;text-transform:uppercase;color:var(--white)}
.btn-gold{background:var(--gold)}
.btn-line{border:2px solid var(--white)}

/* nav */
.site-header{height:67px;background:#1e1e1e}
.brand{position:absolute;left:234px;top:18px;display:flex;align-items:center;gap:8px;font-family:var(--head);font-weight:600;font-size:13px;color:var(--gold)}
.brand-dot{width:30px;height:30px;border-radius:50%;border:2px solid var(--gold)}
.nav{position:absolute;right:235px;top:27px;display:flex;gap:25px;font-family:var(--head);font-size:10px;font-weight:500;text-transform:uppercase;letter-spacing:.5px}

/* hero */
.hero{height:488px}
.hero-photo{position:absolute;inset:0;background:linear-gradient(180deg,#3e3f42 0%,#55575a 35%,#8d8f91 60%,#6c6e70 100%)}
.hero-title{top:122px;font-family:var(--head);font-weight:700;font-size:31px;line-height:41px}
.hero-tag{top:244px;font-family:'Fira Sans Condensed',sans-serif;font-size:21px;letter-spacing:1.5px}

/* services */
.services{height:508px;background:var(--black)}
.card{position:absolute;top:170px;width:232px;height:240px;border:1px solid #5a5a5a;padding:38px 37px 0}
.card.is-active{background:var(--gold);border-color:var(--gold)}
.card h3{font-family:var(--head);font-weight:500;font-size:13.5px;color:var(--gold);margin-bottom:14px}
.card.is-active h3{color:var(--white)}
.card p{font-size:11px;line-height:19px;color:#b5b5b5}
.card.is-active p{color:#fff3d6}
.card .rule{width:24px;height:2px;background:var(--gold);margin:30px 0 14px}
.card.is-active .rule{background:#5b3e00}
.card .more{font-family:var(--head);font-size:9px;font-weight:600;letter-spacing:.5px}

/* about */
.about{height:527px;background:var(--black)}
.about-panel{position:absolute;left:0;top:0;width:797px;height:527px;background:var(--charcoal)}
.about-title{left:234px;top:119px;font-family:var(--head);font-weight:600;font-size:25px;line-height:30px;width:330px}
.about-text{left:234px;top:262px;width:320px;font-size:11px;line-height:19px;color:#b5b5b5}
.about-photo{left:609px;top:74px;width:508px;height:377px;background:linear-gradient(180deg,#7d8086 0%,#a3a39c 40%,#dcdcdc 70%,#c4c4c4 100%)}

/* cta */
.cta{height:183px;background:var(--gold);overflow:hidden}
.cta h2{left:234px;top:38px;font-family:var(--head);font-weight:600;font-size:24px;line-height:30px}
.cta p{left:234px;top:105px;width:430px;font-size:10.5px;line-height:19px}

/* projects */
.projects{height:964px;background:var(--black)}
.tile{position:absolute}
.overlay{position:absolute;left:16px;top:18px;width:320px;height:380px;background:rgba(244,177,27,.88);display:flex;flex-direction:column;align-items:center;justify-content:center;gap:8px}
.overlay small{font-family:var(--head);font-size:9px;letter-spacing:1.5px;font-weight:600}
.overlay strong{font-family:var(--head);font-size:13px;font-weight:500}

/* blog */
.blog{height:466px;background:var(--black)}
.post{position:absolute;top:127px;width:232px}
.post-photo{height:151px;background:linear-gradient(180deg,#3b4e6b 0%,#8f9aa3 30%,#c6b476 55%,#b5a56b 100%)}
.post time{display:block;margin-top:20px;font-size:8px;color:var(--muted)}
.post h3{margin-top:6px;font-family:var(--head);font-weight:400;font-size:13px;line-height:22px}
.post a{display:block;margin-top:2px;font-size:9px;color:var(--gold);text-decoration:none}

/* newsletter */
.newsletter{height:306px;background:var(--charcoal)}
.map{left:0;top:0;width:466px;height:306px;background:linear-gradient(135deg,#8b8b8b,#7a7a7a)}
.field-label{font-family:var(--head);font-size:9px;font-weight:500;text-transform:uppercase}
.field{position:absolute;top:212px;width:169px;border-bottom:1px solid #777;padding-bottom:5px;font-size:8px;font-style:italic;color:#6e6e6e;padding-left:8px}

/* footer */
.site-footer{height:199px;background:var(--footer)}
.col h4{font-family:var(--head);font-size:10px;font-weight:600;color:var(--gold);text-transform:uppercase;margin-bottom:11px}
.col li{list-style:none;font-size:10px;color:#bdbdbd;height:25px;display:flex;align-items:flex-start;gap:10px}
.ico{width:15px;height:15px;border-radius:50%;background:var(--gold);display:flex;align-items:center;justify-content:center;flex-shrink:0;margin-top:-2px}
.copyright{height:42px;background:var(--gold);display:flex;align-items:center;justify-content:center;font-size:8px}
</style>
</head>
<body>
<div class="page">

<header class="site-header">
  <div class="brand"><span class="brand-dot"></span>Harbor Seal Works</div>
  <nav class="nav"><span>Home</span><span>About Us</span><span>Services</span><span>Our Projects</span><span>Blog</span><span>Contact</span></nav>
</header>

<section class="hero">
  <div class="hero-photo" role="img" aria-label="Photo of a freshly coated industrial metal roof under an overcast sky"></div>
  <h1 class="abs center hero-title">Specializing in Spray Foam and Roof<br>Restoration Coating Systems for over 20-years</h1>
  <p class="abs center hero-tag">“SOLUTIONS WITH INTEGRITY”</p>
  <span class="btn btn-gold" style="left:466px;top:328px;width:124px;height:36px">Contact Us</span>
  <span class="btn" style="left:610px;top:328px;width:124px;height:36px;border:2px solid var(--gold)">Read More</span>
</section>

<section class="services">
  <p class="abs center label" style="top:84px">Service</p>
  <h2 class="abs center title" style="top:100px">What We Propose</h2>
  <article class="card is-active" style="left:234px">
    <h3>Foam Insulation</h3>
    <p>Lorem ipsum dolor sit amet, consectetur adipiscing elit, sed do eiusmod tempor incididunt ut labore</p>
    <div class="rule"></div><span class="more">Read More</span>
  </article>
  <article class="card" style="left:484px">
    <h3>Foam Roof</h3>
    <p>Lorem ipsum dolor sit amet, consectetur adipiscing elit, sed do eiusmod tempor incididunt ut labore</p>
    <div class="rule"></div><span class="more">Read More</span>
  </article>
  <article class="card" style="left:734px">
    <h3>Roof Restoration/Coating</h3>
    <p>Lorem ipsum dolor sit amet, consectetur adipiscing elit, sed do eiusmod tempor incididunt ut labore</p>
    <div class="rule"></div><span class="more">Read More</span>
  </article>
</section>

<section class="about">
  <div class="about-panel"></div>
  <p class="abs label" style="left:234px;top:98px">Who We Are</p>
  <h2 class="abs about-title">Lorem ipsum dolor sit amet, consectetur adipisicing elit labore et dolore</h2>
  <p class="abs about-text">Ut enim ad minim veniam, quis nostrud exercitation ullamco laboris nisi ut aliquip ex ea commodo consequat. Duis aute irure dolor in reprehenderit in voluptate velit esse cillum dolore eu fugiat nulla pariatur. Excepteur sint occaecat cupidatat non proident.</p>
  <span class="btn btn-gold" style="left:234px;top:391px;width:127px;height:39px">Read More</span>
  <div class="abs about-photo" role="img" aria-label="Photo of a crew member spraying coating on a metal roof"></div>
</section>

<section class="cta">
  <svg class="abs" style="left:0;top:0" width="1200" height="183" viewBox="0 0 1200 183" aria-hidden="true">
    <path d="M100 0 C160 40 260 20 330 70 C400 120 430 160 470 183 L1200 183 L1200 0 Z" fill="var(--gold-light)"/>
    <path d="M520 0 C600 40 720 60 760 120 C790 160 880 170 1200 150 L1200 0 Z" fill="var(--gold)"/>
  </svg>
  <h2 class="abs">Duis aute irure dolor in reprehenderit<br>in voluptate velit esse</h2>
  <p class="abs">Nemo enim ipsam voluptatem quia voluptas sit aspernatur aut odit aut fugit, sed quia consequuntur magni dolores eos qui ratione voluptatem sequi nesciunt.</p>
  <span class="btn btn-line" style="left:827px;top:68px;width:138px;height:43px">Contact Us</span>
</section>

<section class="projects">
  <p class="abs center label" style="top:93px">Our Projects</p>
  <h2 class="abs center title" style="top:115px">Lorem ipsum</h2>
  <div class="tile" style="left:234px;top:174px;width:356px;height:418px;background:linear-gradient(180deg,#5f6368 0%,#8a8c8c 35%,#d8d8d8 60%,#b0b0b0 100%)" role="img" aria-label="Photo of a coated roof beside an industrial plant"></div>
  <div class="tile" style="left:234px;top:611px;width:356px;height:205px;background:linear-gradient(180deg,#8d8a7e 0%,#d6d2c2 50%,#9e9e9e 100%)" role="img" aria-label="Photo of a warehouse interior with spray foam insulated walls"></div>
  <div class="tile" style="left:610px;top:174px;width:355px;height:205px;background:linear-gradient(180deg,#6f7276 0%,#a2a4a6 40%,#dedede 75%,#c3c3c3 100%)" role="img" aria-label="Photo of a large white coated roof"></div>
  <div class="tile" style="left:610px;top:399px;width:355px;height:417px;background:linear-gradient(180deg,#2c4a7a 0%,#b39a63 30%,#c9b488 100%)" role="img" aria-label="Photo of a metal building roof being restored">
    <div class="overlay"><small>DOLOREM IPSUM</small><strong>NUMQUAM MODI TEMPORA</strong></div>
  </div>
  <span class="btn btn-line" style="left:537px;top:865px;width:126px;height:38px">More Projects</span>
</section>

<section class="blog">
  <p class="abs center label" style="top:53px">Blog</p>
  <h2 class="abs center title" style="top:74px">Latest Post</h2>
  <article class="post" style="left:234px">
    <div class="post-photo" role="img" aria-label="Photo of a foam roof with a traffic cone"></div>
    <time>Jan 15 2020</time>
    <h3>Duis aute irure dolor in reprehenderit voluptate velit esse</h3>
    <a href="#">Read More</a>
  </article>
  <article class="post" style="left:484px">
    <div class="post-photo" role="img" aria-label="Photo of a foam roof with a traffic cone"></div>
    <time>Jan 15 2020</time>
    <h3>Duis aute irure dolor in reprehenderit voluptate velit esse</h3>
    <a href="#">Read More</a>
  </article>
  <article class="post" style="left:734px">
    <div class="post-photo" role="img" aria-label="Photo of a foam roof with a traffic cone"></div>
    <time>Jan 15 2020</time>
    <h3>Duis aute irure dolor in reprehenderit voluptate velit esse</h3>
    <a href="#">Read More</a>
  </article>
</section>

<section class="newsletter">
  <div class="abs map" role="img" aria-label="Grey city street map showing the office location"></div>
  <p class="abs label" style="left:483px;top:67px">Subscribe to our newsletter</p>
  <h2 class="abs" style="left:483px;top:84px;font-family:var(--head);font-weight:400;font-size:24px">To stay in touch</h2>
  <span class="abs field-label" style="left:483px;top:179px">Name</span>
  <span class="abs field-label" style="left:671px;top:179px">E-mail address</span>
  <span class="field" style="left:483px">your name</span>
  <span class="field" style="left:671px">your e-mail</span>
  <span class="btn btn-gold" style="left:859px;top:187px;width:106px;height:36px">Register</span>
</section>

<footer class="site-footer">
  <div class="brand" style="top:51px"><span class="brand-dot"></span>Harbor Seal Works</div>
  <div class="abs col" style="left:422px;top:46px">
    <h4>Company</h4>
    <ul><li>About Us</li><li>Our Team</li><li>Services</li><li>Contact</li></ul>
  </div>
  <div class="abs col" style="left:546px;top:46px">
    <h4>Resources</h4>
    <ul><li>Get a spray foam estimate</li><li>Lorem ipsum consectetur</li><li>Adipisicing elit</li><li>Eiusmod ut labore</li></ul>
  </div>
  <div class="abs col" style="left:734px;top:46px">
    <h4>Get in touch</h4>
    <ul>
      <li><span class="ico"><svg width="8" height="9" viewBox="0 0 8 9"><path d="M4 0a3 3 0 0 1 3 3c0 2.2-3 6-3 6S1 5.2 1 3a3 3 0 0 1 3-3z" fill="#fff"/></svg></span>157 5th Lorem Ipsum, 1234 NYC</li>
      <li><span class="ico"><svg width="8" height="8" viewBox="0 0 8 8"><path d="M1 .5l1.6-.3 1 2-1 .8a5 5 0 0 0 2.4 2.4l.8-1 2 1L7.5 7C4 7.3.7 4 1 .5z" fill="#fff"/></svg></span>1 555-014-2290</li>
      <li><span class="ico"><svg width="8" height="6" viewBox="0 0 8 6"><rect x=".5" y=".5" width="7" height="5" fill="none" stroke="#fff"/><path d="M.5.5L4 3.3 7.5.5" fill="none" stroke="#fff"/></svg></span>hello@harborsealworks.example</li>
    </ul>
  </div>
</footer>

<div class="copyright">©2020 by Harbor Seal Works, LLC. All rights reserved</div>

</div>
</body>
</html>
```